Quiet Harbor Coffee - Full Brand Packaging Suite (Pods, Boxes, Bags)

Quiet Harbor Coffee is commissioning a complete packaging system for our 12‑roast specialty coffee collection. Each roast is inspired by a Christian ministry, and every package must follow a consistent storytelling structure across all formats: single‑serve pod lids, 12‑count and 24‑count pod boxes, 12 oz bags, and 2 lb bags.Packaging Formats Needed:• Single‑Serve Pod Lids: Circular design featuring roast name, roast type, ministry inspiration, and color theme.
• 12‑Count & 24‑Count Pod Boxes: Full panel design (front, back, sides, top) matching the roast’s identity and ministry story.
• 12 oz Bag: Vertical layout with strong shelf presence, roast color theme, ministry spotlight, and brand story.
• 2 lb Bag: Same design language as the 12 oz bag, scaled appropriately.
Required Panel Structure (applies to every roast):• Front Panel:• Roast Name
• Roast Type
• “Inspired By: [Ministry Name]”
• “Mission Driven | Fueling Global Impact”
• “Brew it. Share it. Fuel the Mission.”

• Side A — Roast Story:
A short, emotionally resonant description connecting the roast’s flavor profile or theme to the ministry’s impact.
• Side B — Ministry Spotlight:
Ministry name, mission summary, and a “Scan to Give” callout with website link.
• Back Panel:• Flavor Notes
• Origin
• Quiet Harbor Coffee Story (provided text stays consistent across all roasts)
• Statement of giving: “50% of net proceeds support our ministry partners + 10% of gross sales from each roast go directly to the ministry it represents.”

Brand Identity:
Quiet Harbor Coffee blends premium specialty coffee with faith‑driven purpose. Designs should feel clean, premium, unified, and visually distinct per roast through color, tone, and ministry theme.Deliverables:• Print‑ready files for all packaging formats
• Editable source files
• Cohesive color system across all 12 roasts
• Consistent layout structure across lids, boxes, and bags
Goal:
Create a unified, premium packaging system that elevates each roast’s identity, communicates its ministry partnership, and strengthens the mission‑driven heart of Quiet Harbor Coffee.

Target Market(s)

Churches

Industry/Entity Type

Churches, ministries, Christian’s

Requirements
Must have
• I’d like the design to look like the AI GENERATED image I had made of the packaging. It looks classy and clean.
Should not have
• Colorful palette, silly pictures, cartons, mascots

```html
<!DOCTYPE html>
<html lang="en">
<head>
<meta charset="UTF-8">
<title>Quiet Harbor Coffee – Steadfast Dawn Box Panels</title>
<link href="https://fonts.googleapis.com/css2?family=Libre+Baskerville:wght@400;700&family=Oswald:wght@400;500;600&display=swap" rel="stylesheet">
<style>
  :root {
    --stage: #0e0e0e;
    --panel: #141414;
    --panel-edge: #1f1f1f;
    --ink-light: #e8e8e8;
    --ink-soft: #b5b5b5;
    --ink-muted: #7c7c7c;
    --gold-light: #f4d35e;
    --gold-mid: #d9a521;
    --gold-deep: #a8741a;
  }
  * { box-sizing: border-box; margin: 0; padding: 0; }
  html, body {
    width: 1200px; height: 1200px; overflow: hidden;
    background: var(--stage);
  }
  .canvas {
    position: relative; width: 1200px; height: 1200px;
    background: radial-gradient(ellipse at 50% 55%, #1a1a1a 0%, var(--stage) 70%);
  }
  .dieline {
    position: absolute; left: 130px; top: 290px;
    display: flex; height: 620px;
  }
  .panel {
    height: 100%;
    background: var(--panel);
    border: 1px solid var(--panel-edge);
  }
  /* Side panel – back copy */
  .panel-side {
    width: 300px;
    display: flex; flex-direction: column; align-items: center;
    padding: 70px 28px 0;
    font-family: "Oswald", sans-serif; font-weight: 400;
    color: var(--ink-light); font-size: 13px; letter-spacing: 0.3px;
    text-transform: uppercase; text-align: center; line-height: 2.1;
  }
  .side-block { margin-bottom: 40px; }
  /* Front panel */
  .panel-front {
    width: 640px;
    display: flex; flex-direction: column; align-items: center;
    padding-top: 60px;
  }
  .brand-name {
    display: flex; align-items: center; gap: 12px;
    font-family: "Oswald", sans-serif; font-weight: 600;
    font-size: 40px; letter-spacing: 2px; text-transform: uppercase;
    color: var(--ink-light); line-height: 1;
  }
  .brand-mark {
    width: 18px; height: 18px; border-radius: 50%;
    background: var(--ink-light);
  }
  .roast-name {
    margin-top: 44px;
    font-family: "Libre Baskerville", serif; font-weight: 700;
    font-size: 58px; line-height: 1.1; text-align: center;
    text-transform: uppercase; letter-spacing: 1px;
    background: linear-gradient(90deg, var(--gold-mid) 0%, var(--gold-light) 45%, var(--gold-deep) 100%);
    -webkit-background-clip: text; background-clip: text; color: transparent;
  }
  .roast-type {
    margin-top: 10px;
    font-family: "Libre Baskerville", serif; font-weight: 700;
    font-size: 21px; letter-spacing: 1.5px; text-transform: uppercase;
    color: var(--ink-light);
  }
  .gold-rule {
    margin-top: 20px; width: 480px; height: 5px;
    background: linear-gradient(90deg, var(--gold-mid), var(--gold-light) 50%, var(--gold-deep));
  }
  .inspired-by {
    margin-top: 20px;
    font-family: "Libre Baskerville", serif; font-weight: 400;
    font-size: 16px; letter-spacing: 1px;
    color: var(--gold-mid);
  }
  .mission-line {
    margin-top: 8px;
    font-family: "Oswald", sans-serif; font-weight: 500;
    font-size: 14px; letter-spacing: 2px; text-transform: uppercase;
    color: var(--ink-soft);
  }
  .net-weight {
    margin-top: 26px;
    font-family: "Oswald", sans-serif; font-weight: 400;
    font-size: 22px; letter-spacing: 2px; text-transform: uppercase;
    color: var(--ink-muted);
  }
  .tagline {
    margin-top: 10px;
    font-family: "Oswald", sans-serif; font-weight: 500;
    font-size: 12px; letter-spacing: 1px; text-transform: uppercase;
    color: var(--ink-light);
  }
  .call-to-action {
    margin-top: 10px;
    font-family: "Oswald", sans-serif; font-weight: 500;
    font-size: 12px; letter-spacing: 1px; text-transform: uppercase;
    color: var(--gold-mid);
  }
</style>
</head>
<body>
<main class="canvas">
  <div class="dieline">
    <section class="panel panel-side" aria-label="Back panel">
      <div class="side-block">
        <p>Flavor notes: caramel, honey, soft citrus</p>
        <p>Origin: Colombia &amp; Brazil blend</p>
      </div>
      <div class="side-block">
        <p>[Quiet Harbor Coffee brand story —</p>
        <p>drop in your existing fixed copy]</p>
      </div>
      <div class="side-block">
        <p>50% of net proceeds support our ministry partners.</p>
        <p>10% of gross sales from this roast go directly to Lantern Gate Ministries.</p>
      </div>
    </section>
    <section class="panel panel-front" aria-label="Front panel">
      <div class="brand-name"><span class="brand-mark"></span>Quiet Harbor Coffee</div>
      <h1 class="roast-name">Steadfast<br>Dawn</h1>
      <p class="roast-type">Premium Single Origin</p>
      <div class="gold-rule"></div>
      <p class="inspired-by">Inspired By: Lantern Gate Ministries</p>
      <p class="mission-line">Mission Driven | Fueling Global Impact</p>
      <p class="net-weight">Dark Roast | Net Wt. 12 oz (340g)</p>
      <p class="tagline">Born of faith, roasted for purpose</p>
      <p class="call-to-action">Brew it. Share it. Fuel the Mission.</p>
    </section>
  </div>
</main>
</body>
</html>
```